Bright Horizon Games Fundraising Event- Climb Along Today!

Create a postcard that can be printed, and also repurposed for website graphics- this is an invitation and the call to action is to visit our website and purchase tickets.
Project brief is attached.
Bright Horizon National Games logo is attached.
Leave space for a sponsor logo to be added.
This is a once in a lifetime opportunity to ride the Harborview Sky Loop with some of the biggest names in Seattle!
Design should convey a sense of urgency to get ride tickets with celebrity of their choice.
Images for use are included.
Target Market(s)
Bright Horizon Games Supporters, Fans of our Celebrity Guests, Fans of outdoor/live music
Industry/Entity Type
Non Profit
Font styles to use
Other font styles liked:
- Ubuntu or Arial
Requirements
Must have
- Event name, date, time, location, National Games logo
- Space to add a sponsor logo at a later time
Nice to have
- Creative way to show the 2 different purchase prices and benefits

```html
<!DOCTYPE html>
<html lang="en">
<head>
<meta charset="utf-8">
<title>Bright Horizon Games – Climb Along Today! Postcard</title>
<link href="https://fonts.googleapis.com/css2?family=Ubuntu:wght@400;500;700&family=Arimo:wght@400;700&display=swap" rel="stylesheet">
<style>
  :root {
    --purple-deep: #3d1d58;
    --purple: #6b2d90;
    --indigo: #4a4aa5;
    --indigo-dark: #2f3192;
    --teal: #2fb596;
    --teal-dark: #23a184;
    --paper: #ffffff;
    --mist: #ececee;
    --canvas: #f2f0ec;
    --ink-light: #ffffff;
  }
  * { box-sizing: border-box; margin: 0; padding: 0; }
  html, body { width: 1200px; height: 850px; overflow: hidden; }
  body { background: var(--canvas); font-family: "Ubuntu", Arial, sans-serif; position: relative; }

  .postcard {
    position: absolute; top: 274px; width: 394px; height: 304px;
    overflow: hidden; background: var(--paper);
    box-shadow: 0 1px 3px rgba(0,0,0,.18);
  }
  .postcard--front { left: 188px; background: var(--mist); }
  .postcard--back { left: 620px; }
  .postcard__shapes { position: absolute; inset: 0; }

  /* Front */
  .headline {
    position: absolute; left: 12px; top: 11px; color: var(--ink-light);
    font-weight: 700; line-height: .92; text-transform: uppercase; z-index: 2;
  }
  .headline__top { display: block; font-size: 35px; letter-spacing: -.5px; }
  .headline__bottom { display: block; font-size: 26px; margin-left: 16px; margin-top: 1px; }
  .headline__bottom small { font-size: 15px; font-weight: 500; margin-right: 3px; }

  .brand {
    position: absolute; display: flex; align-items: center; gap: 6px;
    color: var(--purple); font-weight: 700; font-family: "Ubuntu", Arial, sans-serif;
  }
  .brand__dot { flex: none; border-radius: 50%; background: var(--teal); }
  .brand--front { left: 250px; top: 17px; font-size: 10px; line-height: 1.15; width: 120px; }
  .brand--front .brand__dot { width: 16px; height: 16px; }

  .invite {
    position: absolute; right: 19px; top: 69px; width: 160px;
    color: var(--ink-light); text-align: right; font-size: 12px; line-height: 1.15;
  }
  .invite__lead { font-size: 13px; }
  .invite__small { font-size: 10px; }

  .venue {
    position: absolute; right: 6px; top: 119px; display: flex; align-items: center; gap: 3px;
    color: var(--teal-dark); font-size: 8.5px; font-weight: 700; white-space: nowrap;
  }
  .when {
    position: absolute; left: 245px; top: 140px; width: 145px; text-align: center;
    color: var(--ink-light); font-weight: 700;
  }
  .when__date { font-size: 12.5px; }
  .when__time { font-size: 9.5px; margin-top: 3px; }

  .sponsor-slot {
    position: absolute; left: 281px; top: 229px;
    color: var(--indigo-dark); font-size: 11px; font-weight: 700;
  }
  .web-link {
    position: absolute; left: 22px; top: 278px; display: flex; align-items: center; gap: 6px;
    color: var(--ink-light); font-size: 8.5px;
  }

  /* Back */
  .details { position: absolute; left: 8px; top: 27px; width: 160px; color: var(--ink-light); font-family: "Arimo", Arial, sans-serif; }
  .details__title { font-family: "Ubuntu", Arial, sans-serif; font-weight: 700; color: var(--purple); font-size: 17px; line-height: 18px; }
  .details__note { font-size: 8px; line-height: 10px; margin-top: 2px; }
  .details__subtitle { font-family: "Ubuntu", Arial, sans-serif; font-weight: 700; color: var(--purple); font-size: 14px; line-height: 17px; margin: 5px 0 7px; }
  .ticket__name { font-family: "Ubuntu", Arial, sans-serif; font-weight: 700; font-size: 12px; line-height: 14px; }
  .ticket__perks { list-style: none; font-size: 8px; line-height: 12px; margin-bottom: 6px; }
  .ticket__perks li { position: relative; padding-left: 9px; }
  .ticket__perks li::before {
    content: ""; position: absolute; left: 1px; top: 3px; width: 3px; height: 5px;
    border: solid var(--purple); border-width: 0 1.4px 1.4px 0; transform: rotate(40deg);
  }

  .brand--back { left: 222px; top: 34px; font-size: 8.5px; line-height: 1.1; width: 62px; flex-direction: column; text-align: center; }
  .brand--back .brand__dot { width: 14px; height: 14px; }
  .stamp-box { position: absolute; left: 290px; top: 25px; width: 82px; height: 68px; border: 1px solid #555; }
  .address-line { position: absolute; left: 190px; width: 182px; border-top: 1px solid #777; }
</style>
</head>
<body>

<article class="postcard postcard--front" aria-label="Postcard front">
  <svg class="postcard__shapes" viewBox="0 0 394 304" width="394" height="304">
    <defs>
      <clipPath id="badge-clip"><circle cx="335" cy="60" r="125"/></clipPath>
      <linearGradient id="photo-tone" x1="0" y1="0" x2="1" y2="1">
        <stop offset="0" stop-color="#5a3a6e"/>
        <stop offset=".55" stop-color="#3a2a3e"/>
        <stop offset="1" stop-color="#231a26"/>
      </linearGradient>
    </defs>
    <rect x="0" y="0" width="215" height="304" fill="var(--purple-deep)"/>
    <ellipse cx="80" cy="150" rx="125" ry="160" fill="url(#photo-tone)" role="img" aria-label="Photo of an athlete hugging her coach in celebration"/>
    <ellipse cx="80" cy="150" rx="125" ry="160" fill="none" stroke="var(--purple)" stroke-width="7"/>
    <g clip-path="url(#badge-clip)">
      <rect x="200" y="-70" width="200" height="260" fill="var(--paper)"/>
      <rect x="200" y="56" width="200" height="3" fill="var(--indigo)"/>
      <rect x="200" y="65" width="200" height="52" fill="var(--indigo)"/>
      <rect x="200" y="134" width="200" height="60" fill="var(--indigo)"/>
    </g>
    <circle cx="335" cy="60" r="125" fill="none" stroke="var(--teal)" stroke-width="4"/>
    <path d="M0 304 V248 C70 236 120 262 180 246 C240 230 300 212 394 206 V304 Z" fill="var(--paper)"/>
    <path d="M210 240 C230 270 232 290 230 304 L0 304 V262 C80 254 150 254 210 240 Z" fill="var(--teal)"/>
    <path d="M0 250 C70 238 120 262 180 246 C240 230 300 212 394 204" fill="none" stroke="var(--purple)" stroke-width="7"/>
    <path d="M212 240 C230 262 234 286 232 304" fill="none" stroke="var(--indigo)" stroke-width="2"/>
  </svg>

  <h1 class="headline">
    <span class="headline__top">Climb</span>
    <span class="headline__bottom"><small>Along</small>Today!</span>
  </h1>

  <div class="brand brand--front">
    <span class="brand__dot"></span>
    <span>Bright Horizon National Games</span>
  </div>

  <p class="invite">
    <span class="invite__lead">A party to benefit</span><br>
    for the 2018<br>
    <span class="invite__small">Bright Horizon National Games</span>
  </p>

  <p class="venue">
    <svg width="9" height="11" viewBox="0 0 10 12" aria-hidden="true"><path d="M5 11 C2 7 1 5.5 1 4 A4 4 0 0 1 9 4 C9 5.5 8 7 5 11 Z" fill="none" stroke="currentColor" stroke-width="1.2"/><circle cx="5" cy="4" r="1.4" fill="currentColor"/></svg>
    Harborview Waterfront- Dock 12
  </p>

  <div class="when">
    <p class="when__date">THURSDAY, MAY 25</p>
    <p class="when__time">Time- 7:00 pm – 10 pm</p>
  </div>

  <p class="sponsor-slot">Sponsor:</p>

  <p class="web-link">
    <svg width="9" height="9" viewBox="0 0 10 10" aria-hidden="true"><circle cx="5" cy="5" r="4.3" fill="none" stroke="#fff" stroke-width="1"/><ellipse cx="5" cy="5" rx="1.9" ry="4.3" fill="none" stroke="#fff" stroke-width=".8"/><line x1=".7" y1="5" x2="9.3" y2="5" stroke="#fff" stroke-width=".8"/></svg>
    www.BrightHorizonGames.org/Party
  </p>
</article>

<article class="postcard postcard--back" aria-label="Postcard back">
  <svg class="postcard__shapes" viewBox="0 0 395 304" width="395" height="304" aria-hidden="true">
    <path d="M0 0 H182 C198 40 212 100 200 170 C192 220 168 260 175 304 H0 Z" fill="var(--teal)"/>
    <path d="M182 0 C198 40 212 100 200 170 C192 220 168 260 175 304" fill="none" stroke="var(--purple)" stroke-width="6"/>
  </svg>

  <section class="details">
    <h2 class="details__title">Event Details</h2>
    <p class="details__note">Live Entertainment provided by:<br>The Tidewater Big Band</p>
    <h3 class="details__subtitle">Two ways to be there</h3>

    <div class="ticket">
      <p class="ticket__name">1.$150 Party Ticket</p>
      <ul class="ticket__perks">
        <li>Entry to party</li>
        <li>Free beer, wine and Hors d'oeuvres</li>
        <li>Mingle with special Celebrity Guests</li>
        <li>Support the Mission of the Bright Horizon National Games</li>
      </ul>
    </div>
    <div class="ticket">
      <p class="ticket__name">2.$250 Ride Ticket</p>
      <ul class="ticket__perks">
        <li>Entry to party</li>
        <li>Free beer, wine and Hors d'oeuvres</li>
        <li>Mingle with special Celebrity Guests</li>
        <li>Support the Mission of the Bright Horizon National Games</li>
        <li>Ride the Harborview Sky Loop with a Celebrity Guest of your choice!</li>
      </ul>
    </div>
  </section>

  <div class="brand brand--back">
    <span class="brand__dot"></span>
    <span>Bright Horizon National Games</span>
  </div>

  <div class="stamp-box" aria-label="Stamp area"></div>
  <div class="address-line" style="top:155px"></div>
  <div class="address-line" style="top:182px"></div>
  <div class="address-line" style="top:209px"></div>
</article>

</body>
</html>
```